Business card for medical clinic

I need an upmarket, modern medical/health business card for my clinic

Contact Information for Business Card

name, address, email, qr code

```html
<!DOCTYPE html>
<html lang="en">
<head>
<meta charset="utf-8">
<title>Meridian Care Clinic – Business Card</title>
<link href="https://fonts.googleapis.com/css2?family=Montserrat:wght@400;500;700&display=swap" rel="stylesheet">
<style>
  :root {
    --page-bg: #e6e7ea;
    --navy: #1f2846;
    --brand-blue: #2a7fc0;
    --ink: #1d1d1f;
    --paper: #ffffff;
    --on-navy: #ffffff;
  }
  * { box-sizing: border-box; margin: 0; padding: 0; }
  html, body {
    width: 1200px;
    height: 800px;
    overflow: hidden;
    background: var(--page-bg);
    font-family: "Montserrat", sans-serif;
  }
  .canvas {
    width: 1200px;
    height: 800px;
    display: flex;
    align-items: center;
    justify-content: center;
    gap: 50px;
  }
  .card {
    width: 530px;
    height: 303px;
    border-radius: 22px;
    position: relative;
    overflow: hidden;
    box-shadow: 0 6px 18px rgba(0,0,0,0.12);
  }

  /* Back side */
  .card--back {
    background: var(--navy);
    display: flex;
    align-items: center;
    justify-content: center;
  }
  .brand-lockup {
    display: flex;
    align-items: center;
    gap: 18px;
    color: var(--on-navy);
  }
  .brand-lockup__dot {
    width: 22px;
    height: 22px;
    border-radius: 50%;
    background: var(--on-navy);
  }
  .brand-lockup__name {
    font-weight: 500;
    font-size: 30px;
    letter-spacing: 0.12em;
    text-transform: uppercase;
  }

  /* Front side */
  .card--front {
    background: var(--paper);
    padding: 34px 40px;
  }
  .front-brand {
    display: flex;
    align-items: center;
    gap: 10px;
    color: var(--brand-blue);
  }
  .front-brand__dot {
    width: 12px;
    height: 12px;
    border-radius: 50%;
    background: var(--brand-blue);
  }
  .front-brand__name {
    font-weight: 500;
    font-size: 15px;
    letter-spacing: 0.12em;
    text-transform: uppercase;
  }
  .person { margin-top: 30px; }
  .person__name {
    font-weight: 700;
    font-size: 27px;
    color: var(--brand-blue);
    line-height: 1.05;
  }
  .person__role {
    font-size: 13px;
    color: var(--ink);
    margin-top: 4px;
  }
  .address {
    margin-top: 18px;
    font-size: 13px;
    line-height: 1.35;
    color: var(--ink);
    font-style: normal;
  }
  .contact-list {
    list-style: none;
    margin-top: 14px;
  }
  .contact-list__item {
    display: flex;
    align-items: center;
    gap: 10px;
    font-size: 13px;
    color: var(--ink);
    margin-bottom: 6px;
  }
  .contact-list__icon {
    width: 15px;
    height: 15px;
    flex: none;
    color: var(--brand-blue);
  }
</style>
</head>
<body>
<main class="canvas">

  <section class="card card--back" aria-label="Card back">
    <div class="brand-lockup">
      <span class="brand-lockup__dot"></span>
      <span class="brand-lockup__name">Meridian Care Clinic</span>
    </div>
  </section>

  <section class="card card--front" aria-label="Card front">
    <div class="front-brand">
      <span class="front-brand__dot"></span>
      <span class="front-brand__name">Meridian Care Clinic</span>
    </div>

    <div class="person">
      <h1 class="person__name">Daniel Harper</h1>
      <p class="person__role">Managing Director</p>
    </div>

    <address class="address">
      48 Cedar Hollow Road<br>
      Brookfield, TN 37027
    </address>

    <ul class="contact-list">
      <li class="contact-list__item">
        <svg class="contact-list__icon" viewBox="0 0 24 24" aria-hidden="true">
          <path fill="currentColor" d="M6.6 10.8a15.1 15.1 0 0 0 6.6 6.6l2.2-2.2a1 1 0 0 1 1-.25 11.4 11.4 0 0 0 3.6.57 1 1 0 0 1 1 1V20a1 1 0 0 1-1 1A17 17 0 0 1 3 4a1 1 0 0 1 1-1h3.5a1 1 0 0 1 1 1c0 1.25.2 2.45.57 3.57a1 1 0 0 1-.25 1z"/>
        </svg>
        555.214.7730
      </li>
      <li class="contact-list__item">
        <svg class="contact-list__icon" viewBox="0 0 24 24" aria-hidden="true">
          <rect x="2" y="5" width="20" height="14" rx="2" fill="currentColor"/>
          <path d="M3 6l9 7 9-7" fill="none" stroke="#fff" stroke-width="1.6"/>
        </svg>
        hello@meridiancare.com
      </li>
      <li class="contact-list__item">
        <svg class="contact-list__icon" viewBox="0 0 24 24" aria-hidden="true">
          <circle cx="12" cy="12" r="10" fill="currentColor"/>
          <path d="M2 12h20M12 2c3 3 3 17 0 20M12 2c-3 3-3 17 0 20" fill="none" stroke="#fff" stroke-width="1.4"/>
        </svg>
        www.meridiancare.com
      </li>
    </ul>
  </section>

</main>
</body>
</html>
```